Create modern and sleek business card for luxury real estate company

We're a "boutique" real estate office looking for a design that gets across a highly modern luxury brand. Blacks and whites are probably the best colors unless we try a silver foil for the logo. I've attached a version of our current logo here. I'd like to swap out the current font on there with Gotham Light Regular.

I'm looking to have one side of the card have the logo with the space for our agents info on the other side.

Target Market(s)

Young professionals in a "luxury" headspace

Industry/Entity Type

Real estate

Contact Information for Business Card

A place for agent name, cell number, website. The slogan "Simply Rethinking Real Estate".

Font styles to use
Other font styles liked:
• Gotham Regular

Colors

Designer to choose only greyscale colors for use in the design.

Requirements
Must have
• Matte black as the background color. Clean lines and use of contrast. A specific design aspect that will use silver foil.
Nice to have
• Up in the air on integrating a QR code
Should not have
• Any houses or other real estate related design (ex: a clip art house)

```html
<!DOCTYPE html>
<html lang="en">
<head>
<meta charset="utf-8">
<title>Halvern Estates – Business Card</title>
<link rel="stylesheet" href="https://fonts.googleapis.com/css2?family=Lato:wght@300;400;700&display=swap">
<style>
  :root {
    --backdrop: #2b2725;
    --card-black: #141414;
    --card-black-light: #2a2a2a;
    --foil: #e6e6e6;
    --text-white: #f4f4f4;
    --rule-grey: #6a6a6a;
  }
  * { margin: 0; padding: 0; box-sizing: border-box; }
  html, body { width: 1200px; height: 842px; overflow: hidden; }
  body {
    background: var(--backdrop);
    font-family: "Lato", sans-serif;
    color: var(--text-white);
    position: relative;
  }
  .card {
    position: absolute;
    top: 272px;
    width: 520px;
    height: 298px;
    background: radial-gradient(ellipse at 55% 40%, var(--card-black-light), var(--card-black) 75%);
    box-shadow: 0 18px 40px rgba(0,0,0,0.55);
    overflow: hidden;
  }
  .card--contact { left: 50px; }
  .card--brand { left: 630px; }

  /* contact side */
  .band {
    position: absolute;
    left: 0; right: 0;
    height: 13px;
    background: var(--foil);
  }
  .band--top { top: 14px; }
  .band--bottom { bottom: 14px; }
  .contact-block {
    position: absolute;
    left: 0; right: 0;
    top: 52px;
    text-align: center;
  }
  .agent-name {
    font-weight: 400;
    font-size: 17px;
    letter-spacing: 0.5px;
    text-transform: uppercase;
  }
  .agent-title {
    font-weight: 300;
    font-size: 12px;
    margin-top: 1px;
  }
  .rule {
    width: 150px;
    height: 1px;
    background: var(--rule-grey);
    margin: 10px auto;
  }
  .contact-list {
    list-style: none;
    font-weight: 300;
    font-size: 13px;
    line-height: 18px;
  }
  .contact-list b { font-weight: 700; }
  .address {
    font-style: normal;
    font-weight: 300;
    font-size: 13px;
    line-height: 17px;
  }

  /* brand side */
  .tab {
    position: absolute;
    width: 20px;
    height: 52px;
    background: var(--foil);
  }
  .tab--left { left: 12px; top: 168px; }
  .tab--right { right: 12px; top: 78px; }
  .brand-lockup {
    position: absolute;
    left: 0; right: 0;
    top: 0; bottom: 0;
    display: flex;
    align-items: center;
    justify-content: center;
    gap: 16px;
  }
  .brand-circle { display: block; }
  .brand-name {
    font-weight: 400;
    font-size: 27px;
    line-height: 34px;
    letter-spacing: 2px;
    text-transform: uppercase;
    color: var(--foil);
  }
</style>
</head>
<body>

  <section class="card card--contact" role="img" aria-label="Matte black card with fine diagonal pinstripe texture, agent contact side">
    <div class="band band--top"></div>
    <div class="contact-block">
      <h1 class="agent-name">Adrian Cole</h1>
      <p class="agent-title">Managing Director</p>
      <div class="rule"></div>
      <ul class="contact-list">
        <li><b>P:</b> 044-555 010 234</li>
        <li><b>M:</b> 044-555 010 234</li>
        <li><b>E:</b> info@halvern.com</li>
        <li><b>W:</b> www.halvern.com</li>
      </ul>
      <div class="rule"></div>
      <address class="address">12345, Address Goes Here<br>Country Name, 123456</address>
    </div>
    <div class="band band--bottom"></div>
  </section>

  <section class="card card--brand" role="img" aria-label="Matte black card with fine diagonal pinstripe texture, brand side">
    <div class="tab tab--left"></div>
    <div class="tab tab--right"></div>
    <div class="brand-lockup">
      <svg class="brand-circle" width="70" height="70" viewBox="0 0 70 70" aria-hidden="true">
        <circle cx="35" cy="35" r="32" fill="none" stroke="#e6e6e6" stroke-width="3"/>
      </svg>
      <p class="brand-name">Halvern<br>Estates</p>
    </div>
  </section>

</body>
</html>
```